Australian Based Web Development Company Needs a Fresh New Modern Look (logo and responsive website)

We are Coral Web Development, an Australian based web development company looking to give our company a fresh, new and modern look.

We tend to deal with small to medium sized businesses, and want to convey the message that we are professional and capable of developing a solution to any need or problem.

Our specialty is custom development applications, such as, intranets, integration software, and client portals.

We have recently started mobile application development as well (iOS and Android).

You can view our current logo and website on https://www.coralwebdevelopment.example/

As we are looking for both a logo and a website design, we may decide to have the website design completed by a different designer to the winning logo designer.

Target Market(s)

Small to medium enterprise businesses

Industry/Entity Type

It Company

Logo Text

Coral Web Development

Number of Pages Required

2 page

Logo styles of interest
Abstract Logo
Wordmark Logo
Font styles to use
Sans Serif

Colors
85cae6
33b8a4

Requirements
Must have
• Website design - a responsive layout (960-1000px content width), and background image/texture of 2,560px wide. A home page design, and a generic content page design.
• Colours - we like blues, greens (more blue-green like teal) and grey, but we are open to seeing other colours if you feel appropriate.
Nice to have
• Website design - Two websites I like the design style is http://www.mavonstack.example/ and https://www.pilvo.example/au/accounting-software/

```html
<!DOCTYPE html>
<html lang="en">
<head>
<meta charset="utf-8">
<title>Coral Web Development – Mobile Home</title>
<link rel="stylesheet" href="https://fonts.googleapis.com/css2?family=Oswald:wght@400;500;600&family=Open+Sans:wght@400;600&display=swap">
<style>
  :root {
    --teal: #33b8a4;
    --teal-dark: #249c8a;
    --sky: #85cae6;
    --ink: #3a3f44;
    --grey: #8c9196;
    --line: #dfe3e5;
    --paper: #ffffff;
    --stage: #eceff1;
    --hero-a: #c9cccf;
    --hero-b: #8e9296;
    --panel: rgba(38, 42, 46, 0.88);
  }
  * { box-sizing: border-box; margin: 0; padding: 0; }
  html, body { width: 1200px; height: 804px; overflow: hidden; }
  body {
    background: var(--stage);
    font-family: "Open Sans", Arial, sans-serif;
    display: flex;
    align-items: center;
    justify-content: center;
  }
  .screen {
    width: 452px;
    height: 780px;
    background: var(--paper);
    overflow: hidden;
    position: relative;
    box-shadow: 0 6px 24px rgba(0,0,0,0.08);
  }
  .site-header {
    height: 118px;
    padding: 26px 24px 0;
    display: flex;
    justify-content: space-between;
    align-items: flex-start;
  }
  .brand {
    display: flex;
    align-items: center;
    gap: 10px;
    font-family: "Oswald", Arial, sans-serif;
    font-weight: 500;
    font-size: 26px;
    letter-spacing: 0.5px;
    color: var(--teal);
    margin-top: 34px;
  }
  .brand-mark { width: 14px; height: 14px; background: var(--teal); }
  .menu-toggle {
    width: 44px; height: 44px;
    background: var(--teal);
    display: flex; align-items: center; justify-content: center;
  }
  .search {
    position: absolute;
    left: 24px; right: 24px; top: 128px;
    height: 48px;
    border: 4px solid var(--teal);
    background: var(--paper);
    display: flex; align-items: center; justify-content: space-between;
    padding-left: 14px;
    z-index: 2;
  }
  .search-placeholder { color: var(--grey); font-size: 14px; }
  .search-button {
    width: 40px; height: 40px; background: var(--teal);
    display: flex; align-items: center; justify-content: center;
  }
  .hero {
    position: relative;
    height: 320px;
    margin-top: 34px;
  }
  .hero-photo {
    position: absolute; inset: 0;
    background: linear-gradient(160deg, var(--hero-a), var(--hero-b));
  }
  .hero-panel {
    position: absolute;
    left: 50%; top: 146px;
    transform: translateX(-50%);
    width: 300px;
    background: var(--panel);
    color: #fff;
    text-align: center;
    padding: 14px 18px 16px;
  }
  .hero-title {
    font-family: "Oswald", Arial, sans-serif;
    font-weight: 600;
    font-size: 20px;
    line-height: 1.25;
    text-transform: uppercase;
    letter-spacing: 0.5px;
  }
  .hero-text { font-size: 10px; line-height: 1.5; margin-top: 8px; color: #d8dcdf; }
  .slider-arrow {
    position: absolute;
    width: 26px; height: 26px;
    background: var(--teal);
    display: flex; align-items: center; justify-content: center;
  }
  .slider-arrow.prev { left: 18px; bottom: 18px; }
  .slider-arrow.next { right: 18px; top: 70px; }
  .about { text-align: center; padding: 22px 40px 0; }
  .section-title {
    font-family: "Oswald", Arial, sans-serif;
    font-weight: 500;
    font-size: 24px;
    color: var(--ink);
  }
  .section-text {
    font-size: 11px; line-height: 1.6; color: var(--grey);
    margin-top: 10px;
  }
  .service { margin-top: 18px; display: flex; flex-direction: column; align-items: center; }
  .service-label {
    font-family: "Oswald", Arial, sans-serif;
    font-size: 15px; line-height: 1.3; color: var(--ink);
    margin-top: 8px;
  }
</style>
</head>
<body>
  <main class="screen">
    <header class="site-header">
      <div class="brand"><span class="brand-mark"></span>Coral Web Development</div>
      <div class="menu-toggle" aria-label="Menu">
        <svg width="20" height="16" viewBox="0 0 20 16"><rect y="0" width="20" height="3" fill="#fff"/><rect y="6.5" width="20" height="3" fill="#fff"/><rect y="13" width="20" height="3" fill="#fff"/></svg>
      </div>
    </header>

    <form class="search" role="search">
      <span class="search-placeholder">Search</span>
      <span class="search-button">
        <svg width="16" height="16" viewBox="0 0 16 16"><circle cx="6.5" cy="6.5" r="4.5" fill="none" stroke="#fff" stroke-width="2"/><line x1="10" y1="10" x2="14.5" y2="14.5" stroke="#fff" stroke-width="2.2" stroke-linecap="round"/></svg>
      </span>
    </form>

    <section class="hero">
      <div class="hero-photo" role="img" aria-label="Photo of business people standing among large jigsaw puzzle pieces"></div>
      <div class="hero-panel">
        <h1 class="hero-title">We build your website<br>creative &amp; professional</h1>
        <p class="hero-text">Custom intranets, client portals and mobile apps built for growing Australian businesses.</p>
      </div>
      <span class="slider-arrow prev"><svg width="10" height="10" viewBox="0 0 10 10"><path d="M7 1 L3 5 L7 9" fill="none" stroke="#fff" stroke-width="2"/></svg></span>
      <span class="slider-arrow next"><svg width="10" height="10" viewBox="0 0 10 10"><path d="M3 1 L7 5 L3 9" fill="none" stroke="#fff" stroke-width="2"/></svg></span>
    </section>

    <section class="about">
      <h2 class="section-title">Who we are?</h2>
      <p class="section-text">Coral is a small team of developers building intranets, integration software and client portals for businesses of every size, and now crafting apps for phones and tablets.</p>
      <div class="service">
        <svg width="92" height="92" viewBox="0 0 96 96" aria-hidden="true">
          <circle cx="48" cy="48" r="42" fill="none" stroke="var(--line)" stroke-width="6"/>
          <path d="M48 6 A42 42 0 1 1 9 63" fill="none" stroke="var(--teal)" stroke-width="6"/>
          <rect x="30" y="34" width="36" height="28" rx="2" fill="var(--ink)"/>
          <rect x="33" y="41" width="30" height="18" fill="#fff"/>
          <text x="48" y="54" text-anchor="middle" font-family="Oswald, sans-serif" font-size="9" fill="var(--ink)">WWW</text>
          <circle cx="34" cy="37.5" r="1.2" fill="#fff"/><circle cx="38" cy="37.5" r="1.2" fill="#fff"/>
        </svg>
        <p class="service-label">Web Designing<br>&amp; Development</p>
      </div>
    </section>
  </main>
</body>
</html>
```